website design Investment Fund

I am looking for a custom website that will work on desktop computer, tablet device and a cellular device. I have attached the booklet so you can get an idea of the look we are going for. Would like to use the website eventually for crowdfunding. We like the ski racer and mountain climbing designs.

Target Market(s)

Financial Services

Industry/Entity Type

Financial Service

Coding

Coded - Design and coding required

Number of Pages Required

5+ page

Font styles to use
Sans Serif

Requirements
Must have
• Must be viewable on a cell phone and tablet and desktop
Nice to have
• Contact us form

```html
<!DOCTYPE html>
<html lang="en">
<head>
<meta charset="utf-8">
<title>Alder Capital II — Secured Income Fund</title>
<link rel="stylesheet" href="https://fonts.googleapis.com/css2?family=Roboto:wght@300;400;500;700;900&family=Roboto+Condensed:wght@400;700&family=Poppins:wght@300;400;500;600&display=swap">
<style>
:root{
  --blue:#1d3f95;
  --blue-deep:#142d6e;
  --navy:#0f2257;
  --red:#e31b23;
  --red-dark:#b8151c;
  --ink:#1b1c22;
  --text:#3b3f4a;
  --white:#ffffff;
  --snow:#eef2f8;
  --muted:#b9bdc8;
}
*{box-sizing:border-box;margin:0;padding:0}
html,body{width:1200px;height:4376px;overflow:hidden}
body{position:relative;background:var(--white);font-family:"Roboto",Arial,sans-serif;color:var(--text)}
.abs{position:absolute}
.placeholder{position:absolute}

/* header / hero */
.hero{left:0;top:0;width:1200px;height:800px;overflow:hidden}
.hero-bg{left:0;top:0;width:1200px;height:800px;background:linear-gradient(160deg,#4f5560 0%,#8a9099 28%,#c9ced6 52%,#e8ecf1 70%,#6b6157 100%)}
.hero-shape{left:0;top:0}
.brand{left:141px;top:96px;font-family:"Roboto",sans-serif;font-weight:700;font-size:20px;letter-spacing:1px;color:var(--white)}
.nav{left:420px;top:74px;display:flex;gap:0;font-family:"Roboto Condensed",sans-serif;font-size:15px;color:var(--white);text-transform:uppercase}
.nav a{color:inherit;text-decoration:none;margin-right:20px}
.hero-title{left:141px;top:210px;font-weight:900;font-size:50px;line-height:56px;color:var(--white);text-transform:uppercase}
.hero-text{left:141px;top:337px;width:520px;font-size:17px;line-height:30px;color:#eef0f4}
.btn{display:inline-block;font-weight:700;text-transform:uppercase;color:var(--white);text-align:center;border-radius:2px}
.hero-btn{left:141px;top:447px;width:140px;height:43px;line-height:43px;background:var(--blue);font-size:16px;box-shadow:0 3px 8px rgba(0,0,0,.3)}
.dots{left:417px;top:704px;display:flex;gap:8px}
.dots span{width:11px;height:11px;border-radius:50%;background:var(--white)}
.dots span.on{box-shadow:0 0 0 3px rgba(255,255,255,.55);background:#cfd3db}

/* welcome */
.snowfield{left:0;top:740px;width:1200px;height:930px;background:linear-gradient(180deg,#ffffff 0%,#f3f5f9 30%,#e5eaf2 55%,#b7c6e0 75%,#6f8bc4 100%)}
.welcome-title{left:141px;top:818px;font-size:39px;font-weight:400;color:var(--ink)}
.welcome-title b{color:var(--blue);font-weight:700}
.welcome-text{left:141px;top:884px;width:578px;font-size:14.5px;line-height:32px;color:#444}
.read-btn{left:141px;top:1102px;width:128px;height:42px;line-height:42px;background:var(--blue);font-size:15px;font-weight:500}

.contact-card{left:762px;top:804px;width:321px;height:437px;background:var(--blue);box-shadow:0 6px 18px rgba(0,0,0,.25);padding:32px 28px 0 28px}
.contact-card h3{font-family:"Roboto Condensed",sans-serif;font-size:23px;font-weight:700;color:var(--white);text-transform:uppercase}
.contact-card .rule{width:74px;height:2px;background:var(--white);margin:20px 0 25px}
.field{height:36px;background:var(--white);border:1px solid #d4d8e0;margin-bottom:13px;font-size:12.5px;line-height:36px;padding-left:14px;color:#555}
.submit{height:44px;line-height:44px;background:var(--red);font-size:18px;margin-top:7px;display:block}

/* services */
.services-title{left:0;top:1318px;width:1200px;text-align:center;font-size:38px;font-weight:900;color:var(--white);letter-spacing:1px}
.dark-band{left:0;top:1666px;width:1200px;height:910px;background:var(--ink)}
.service-svg{left:0;top:1330px}
.service{text-align:center;color:var(--white)}
.service h4{font-size:18px;font-weight:500;text-transform:uppercase;margin:10px 0 10px}
.service p{font-size:13.5px;line-height:24px}
.svc-left{left:188px;top:1460px;width:232px}
.svc-right{left:779px;top:1460px;width:232px}
.svc-mid{left:464px;top:1584px;width:272px}
.svc-mid h4{font-size:18px;font-weight:700}

/* boutique */
.boutique-frame{left:143px;top:1988px;width:448px;height:400px;border:3px solid var(--red)}
.boutique-photo{left:147px;top:1992px;width:438px;height:390px;background:linear-gradient(135deg,#d9d6d0 0%,#8d8a86 45%,#3e3c3a 100%)}
.boutique h2{font-size:28px;line-height:38px;font-weight:700;color:var(--white);text-transform:uppercase}
.boutique p{font-size:14px;line-height:29px;color:#c9ccd4;margin:10px 0 14px}
.boutique{left:634px;top:2000px;width:460px}

/* team */
.team-title{left:0;top:2632px;width:1200px;text-align:center;font-size:37px;font-weight:400;color:var(--ink)}
.team-title b{font-weight:700}
.team-card{top:2718px;width:220px;height:317px;border-top:3px solid var(--blue)}
.team-photo{left:0;top:0;width:220px;height:236px;background:linear-gradient(180deg,#f2f2f2 0%,#d8d8d8 55%,#2c2c30 100%)}
.team-label{left:0;top:236px;width:220px;height:81px;background:var(--blue);color:var(--white);text-align:center;padding-top:24px}
.team-label strong{display:block;font-size:16px;font-weight:400;text-transform:uppercase}
.team-label span{font-size:12.5px}

/* blog */
.blog-svg{left:0;top:3120px}
.blog-title{left:0;top:3250px;width:1200px;text-align:center;font-size:38px;color:var(--white);font-weight:300}
.blog-title b{font-weight:900}
.blog-rule{left:572px;top:3320px;width:56px;height:3px;background:var(--white)}
.blog-card{top:3369px;width:287px;height:352px;background:var(--white);border-radius:3px;overflow:hidden}
.blog-photo{left:0;top:0;width:287px;height:182px}
.blog-date{left:10px;top:10px;width:44px;height:46px;background:var(--red);color:var(--white);font-family:"Roboto Condensed",sans-serif;font-size:14px;line-height:18px;text-align:center;padding-top:5px}
.blog-body{left:16px;top:206px;width:256px}
.blog-body h5{font-size:17px;line-height:27px;font-weight:700;color:#222}
.blog-body p{font-family:"Poppins",sans-serif;font-size:11.5px;line-height:24px;color:#555;margin-top:12px}

/* footer */
.footer-brand{left:135px;top:4076px;width:190px;text-align:center;font-weight:700;font-size:22px;color:var(--navy)}
.socials{left:163px;top:4140px;display:flex;gap:6px}
.socials span{width:27px;height:27px;border:1.5px solid #333;border-radius:50%}
.foot-col h6{font-family:"Poppins",sans-serif;font-size:17px;font-weight:600;color:#222;text-transform:uppercase}
.news{left:364px;top:3978px;width:275px}
.news p{font-family:"Poppins",sans-serif;font-size:12px;line-height:22px;color:#444;margin:16px 0 12px}
.news .email{height:36px;border:1px solid #ccc;border-radius:18px;font-family:"Poppins",sans-serif;font-size:10.5px;line-height:34px;padding-left:14px;color:#555}
.news .btn{width:134px;height:36px;line-height:36px;border-radius:18px;background:var(--red);font-family:"Poppins",sans-serif;font-size:14px;font-weight:600;margin-top:12px}
.contact-us{left:682px;top:3983px;width:230px}
.contact-row{position:relative;padding-left:38px;font-family:"Poppins",sans-serif;font-size:13.5px;line-height:20px;color:#333;margin-top:16px}
.contact-row svg{position:absolute;left:2px;top:2px}
.links{left:943px;top:3978px}
.links ul{list-style:none;margin-top:14px;padding-left:4px}
.links li{font-family:"Poppins",sans-serif;font-size:12.5px;line-height:27.5px;color:#333}
.foot-rule{left:0;top:4274px;width:1200px;height:1px;background:#ddd}
.copyright{left:0;top:4316px;width:1200px;text-align:center;font-family:"Poppins",sans-serif;font-size:13px;color:#333}
</style>
</head>
<body>

<!-- HERO -->
<section class="abs hero">
  <div class="placeholder hero-bg" role="img" aria-label="Mountain climbers roped together on a snowy ridge beneath rocky peaks and clouds"></div>
  <svg class="abs hero-shape" width="1200" height="800" viewBox="0 0 1200 800" aria-hidden="true">
    <polygon points="0,568 408,770 0,640" fill="#1d3f95"/>
    <polygon points="0,612 408,774 0,666" fill="#e31b23"/>
    <polygon points="0,668 408,774 1200,654 1200,800 0,800" fill="#ffffff"/>
  </svg>
  <div class="abs brand">ALDER CAPITAL II</div>
  <nav class="abs nav">
    <a>Company</a><a>Services</a><a>Clients</a><a>Investors</a><a>Brokers</a><a>Loan Programs</a><a>Contact</a>
  </nav>
  <h1 class="abs hero-title">Alder Capital II<br>Secured Income Fund</h1>
  <p class="abs hero-text">Sed ut perspiciatis unde omnis iste natus error sit voluptatem accusantium doloremque laudantium, totam rem aperiam, eaque ipsa quae ab illo inventore veritatis et quasi</p>
  <a class="abs btn hero-btn">Learn More</a>
  <div class="abs dots"><span class="on"></span><span></span><span></span><span></span></div>
</section>

<!-- WELCOME -->
<div class="placeholder snowfield" role="img" aria-label="Snowy ski slope with a downhill ski racer in a tuck"></div>
<h2 class="abs welcome-title">Welcome to <b>Alder Capital II</b></h2>
<p class="abs welcome-text">Alder Funding &amp; Investment, Inc. is an independent private lender, asset management and advisory firm based in the Mountain West which focuses on quick funding for debt, equity, bridge and land positions on property projects in the $250,000 to $40,000,000 range. As a trusted, steady and growth-minded company with many years of experience across the full spectrum of property finance, we serve clients throughout the western region and neighbouring markets.</p>
<a class="abs btn read-btn">Read More</a>

<form class="abs contact-card">
  <h3>Quick Contact</h3>
  <div class="rule"></div>
  <div class="field">First Name</div>
  <div class="field">Last Name</div>
  <div class="field">Phone</div>
  <div class="field">Email</div>
  <div class="field">Message</div>
  <span class="btn submit">Submit</span>
</form>

<!-- SERVICES -->
<div class="abs dark-band"></div>
<h2 class="abs services-title">OUR SERVICES</h2>
<svg class="abs service-svg" width="1200" height="600" viewBox="0 1330 1200 600" aria-hidden="true">
  <polygon points="304,1338 484,1528 304,1718 124,1528" fill="#1d3f95"/>
  <polygon points="895,1338 1075,1528 895,1718 715,1528" fill="#1d3f95"/>
  <polygon points="600,1395 836,1652 600,1910 364,1652" fill="#c9222a" stroke="#e9e9ea" stroke-width="2"/>
  <circle cx="304" cy="1706" r="13" fill="#fff"/><path d="M301,1700 l6,6 l-6,6" stroke="#1d3f95" stroke-width="2" fill="none"/>
  <circle cx="895" cy="1706" r="13" fill="#fff"/><path d="M892,1700 l6,6 l-6,6" stroke="#1d3f95" stroke-width="2" fill="none"/>
  <circle cx="600" cy="1433" r="16" fill="#fff"/><path d="M597,1426 l7,7 l-7,7" stroke="#c9222a" stroke-width="2.4" fill="none"/>
  <g stroke="#fff" stroke-width="2" fill="none">
    <rect x="280" y="1428" width="7" height="14"/><rect x="291" y="1420" width="7" height="22"/><rect x="302" y="1412" width="7" height="30"/>
    <path d="M278,1414 l14,-10 l8,5 l14,-12"/><circle cx="318" cy="1436" r="8"/>
  </g>
  <g stroke="#fff" stroke-width="2" fill="none">
    <rect x="586" y="1505" width="44" height="28"/><path d="M592,1527 l10,-10 l8,6 l12,-12"/>
    <circle cx="572" cy="1528" r="5"/><path d="M565,1552 v-14 h14 v14"/>
    <circle cx="592" cy="1546" r="4"/><circle cx="606" cy="1546" r="4"/><circle cx="620" cy="1546" r="4"/>
  </g>
  <g stroke="#fff" stroke-width="2" fill="none">
    <circle cx="883" cy="1412" r="7"/><circle cx="907" cy="1412" r="7"/>
    <path d="M870,1444 v-12 a13,13 0 0 1 26,0"/><path d="M894,1444 v-12 a13,13 0 0 1 26,0"/>
  </g>
</svg>
<div class="abs service svc-left">
  <h4>Asset Management</h4>
  <p>Alder provides premier short-term real estate financing in the twelve to twenty four month range. Our detailed oriented team analyzes, underwrites, inspects</p>
</div>
<div class="abs service svc-right">
  <h4>Consulting</h4>
  <p>Alder provides premier short-term real estate financing in the twelve to twenty four month range. Our detailed oriented team analyzes, underwrites, inspects</p>
</div>
<div class="abs service svc-mid">
  <h4>Real Estate Development</h4>
  <p>Alder provides premier short-term real estate financing in the twelve to twenty four month range. Our detailed oriented team analyzes, underwrites, inspects and reviews all facets of the loan transaction documentation. We also generate all escrows agreements and loan documents.</p>
</div>

<!-- BOUTIQUE -->
<div class="abs boutique-frame"></div>
<div class="placeholder boutique-photo" role="img" aria-label="Hands holding a coffee cup and a tablet showing financial charts"></div>
<div class="abs boutique">
  <h2>The Boutique Fund Investors<br>Are Looking For</h2>
  <p>Sed ut perspiciatis unde omnis iste natus error sit voluptatem accusantium doloremque laudantium, totam rem aperiam, eaque ipsa quae ab illo inventore veritatis et quasi architecto beatae vitae dicta sunt explicabo. Nemo enim ipsam</p>
  <h2>Investment Strategy</h2>
  <p>Sed ut perspiciatis unde omnis iste natus error sit voluptatem accusantium doloremque laudantium, totam rem aperiam, eaque ipsa quae ab illo inventore veritatis et quasi architecto beatae vitae dicta sunt explicabo. Nemo enim ipsam</p>
</div>
<svg class="abs" style="left:0;top:2370px" width="1200" height="210" viewBox="0 2370 1200 210" aria-hidden="true">
  <polygon points="0,2474 782,2574 1200,2420 1200,2580 0,2580" fill="#ffffff"/>
  <polygon points="760,2572 1200,2382 1200,2415 790,2574" fill="#e31b23"/>
  <polygon points="740,2572 1200,2410 1200,2422 782,2574" fill="#1d3f95"/>
</svg>

<!-- TEAM -->
<h2 class="abs team-title">OUR <b>TEAM</b></h2>
<div class="abs team-card" style="left:145px">
  <div class="placeholder team-photo" role="img" aria-label="Portrait of Grant Ellison"></div>
  <div class="abs team-label"><strong>Grant Ellison</strong><span>Founder and Fund Manager</span></div>
</div>
<div class="abs team-card" style="left:376px">
  <div class="placeholder team-photo" role="img" aria-label="Portrait of Claire Whitfield"></div>
  <div class="abs team-label"><strong>Claire Whitfield</strong><span>Founder and Managing Partner</span></div>
</div>
<div class="abs team-card" style="left:605px">
  <div class="placeholder team-photo" role="img" aria-label="Portrait of Peter Varga"></div>
  <div class="abs team-label"><strong>Peter Varga</strong><span>Fund Advisor</span></div>
</div>
<div class="abs team-card" style="left:835px">
  <div class="placeholder team-photo" role="img" aria-label="Portrait of Simon Halvorsen"></div>
  <div class="abs team-label"><strong>Simon Halvorsen</strong><span>Chief Investment Officer</span></div>
</div>

<!-- BLOG -->
<svg class="abs blog-svg" width="1200" height="800" viewBox="0 3120 1200 800" aria-hidden="true">
  <polygon points="0,3240 300,3162 1200,3162 1200,3730 800,3910 0,3805" fill="#142d6e"/>
  <polygon points="0,3190 300,3162 0,3235" fill="#1d3f95"/>
  <polygon points="0,3235 300,3162 330,3162 0,3320" fill="#e31b23"/>
  <polygon points="0,3320 330,3162 360,3162 0,3340" fill="#1d3f95"/>
  <polygon points="790,3910 1200,3700 1200,3738 820,3912" fill="#e31b23"/>
  <polygon points="760,3910 1200,3735 1200,3748 800,3912" fill="#1d3f95"/>
</svg>
<h2 class="abs blog-title"><b>LATEST</b> BLOG</h2>
<div class="abs blog-rule"></div>

<article class="abs blog-card" style="left:145px">
  <div class="placeholder blog-photo" role="img" aria-label="Ski racers speeding down a course" style="background:linear-gradient(160deg,#4a6fa8,#dfe6ef 60%,#2b3f6b)"></div>
  <div class="abs blog-date">Oct 01<br>2019</div>
  <div class="abs blog-body"><h5>Sed ut perspiciatis unde omnis iste natus</h5><p>Sed ut perspiciatis unde omnis iste natus error sit voluptatem accusantium doloque laium, totam rem aperiam</p></div>
</article>
<article class="abs blog-card" style="left:457px">
  <div class="placeholder blog-photo" role="img" aria-label="Climber on a rock face above the clouds" style="background:linear-gradient(160deg,#3a3330,#8b93a0 55%,#dfe3ea)"></div>
  <div class="abs blog-date">Oct 01<br>2019</div>
  <div class="abs blog-body"><h5>Sed ut perspiciatis unde omnis iste natus</h5><p>Sed ut perspiciatis unde omnis iste natus error sit voluptatem accusantium doloque laium, totam rem aperiam</p></div>
</article>
<article class="abs blog-card" style="left:768px">
  <div class="placeholder blog-photo" role="img" aria-label="Skier carving a turn below snowy peaks" style="background:linear-gradient(170deg,#3f6fb5,#c9d6e8 55%,#1f2d48)"></div>
  <div class="abs blog-date">Oct 01<br>2019</div>
  <div class="abs blog-body"><h5>Sed ut perspiciatis unde omnis iste natus</h5><p>Sed ut perspiciatis unde omnis iste natus error sit voluptatem accusantium doloque laium, totam rem aperiam</p></div>
</article>

<!-- FOOTER -->
<div class="abs footer-brand">ALDER CAPITAL II</div>
<div class="abs socials"><span></span><span></span><span></span><span></span></div>

<div class="abs foot-col news">
  <h6>Sign up for newsletter</h6>
  <p>Excepteur sint occaecat cupidatat non proident, sunt in culpa qui officia deserunt</p>
  <div class="email">Enter email</div>
  <span class="btn">Subscribe</span>
</div>

<div class="abs foot-col contact-us">
  <h6>Contact Us</h6>
  <div class="contact-row">
    <svg width="16" height="20" viewBox="0 0 16 20"><path d="M8,0 a7,7 0 0 1 7,7 c0,5 -7,13 -7,13 s-7,-8 -7,-13 a7,7 0 0 1 7,-7z" fill="#e31b23"/><circle cx="8" cy="7" r="2.6" fill="#fff"/></svg>
    214 Summit Ridge Road<br>Granite Park, WA, 6020
  </div>
  <div class="contact-row">
    <svg width="16" height="16" viewBox="0 0 16 16"><path d="M3,1 l3,0 l1.5,4 l-2,1.5 a9,9 0 0 0 4,4 l1.5,-2 l4,1.5 l0,3 a2,2 0 0 1 -2,2 a13,13 0 0 1 -12,-12 a2,2 0 0 1 2,-2z" fill="#e31b23"/></svg>
    Phone:<br>808 555 0142
  </div>
  <div class="contact-row">
    <svg width="17" height="13" viewBox="0 0 17 13"><rect x="0" y="0" width="17" height="13" rx="1" fill="#e31b23"/><path d="M1,1 l7.5,6 l7.5,-6" stroke="#fff" stroke-width="1.4" fill="none"/></svg>
    Email:<br>info@aldercapitalii.com
  </div>
</div>

<div class="abs foot-col links">
  <h6>Quick Links</h6>
  <ul><li>Company</li><li>Objective</li><li>Services</li><li>Clients</li><li>Investors</li><li>Brokers</li><li>Contact</li></ul>
</div>

<div class="abs foot-rule"></div>
<p class="abs copyright">Alder Capital II © 2019 All Rights Reserved | Privacy Policy | Terms and Conditions</p>

</body>
</html>
```